Investment company needing business card

We are wanting a business card which looks sharp and easy on the eye. We are thinking of having a business card with the logo embossed on it, to really make it stand out. We will only have a small amount of information of the business card, person's name, position, email address and phone number

Contact Information for Business Card

Danielle Frost
Executive Assistant
+64 21 473 5162
danielf@harwickpartners.co.nz

Requirements
Must have
• Embossed logo
Should not have
• Not to be busy

```html
<!DOCTYPE html>
<html lang="en">
<head>
<meta charset="utf-8">
<title>Harwick Partners – Business Card</title>
<link rel="stylesheet" href="https://fonts.googleapis.com/css2?family=Lato:wght@400;700&display=swap">
<style>
  :root {
    --backdrop: #e9e7e3;
    --card-white: #f6f6f4;
    --brand-green: #22c08e;
    --swoosh-grey: #8a8b8d;
    --rule-grey: #9a9b9d;
    --ink-white: #ffffff;
  }
  * { margin: 0; padding: 0; box-sizing: border-box; }
  html, body {
    width: 1200px;
    height: 780px;
    overflow: hidden;
    background: var(--backdrop);
  }
  .canvas {
    position: relative;
    width: 1200px;
    height: 780px;
    display: flex;
    align-items: center;
    justify-content: center;
  }
  .business-card {
    position: relative;
    width: 1000px;
    height: 580px;
    background: var(--card-white);
    border-radius: 6px;
    overflow: hidden;
    box-shadow: 0 14px 40px rgba(0,0,0,0.18);
  }
  .card-shapes {
    position: absolute;
    inset: 0;
    width: 100%;
    height: 100%;
  }
  .brand-lockup {
    position: absolute;
    left: 70px;
    top: 220px;
    display: flex;
    align-items: center;
    gap: 22px;
  }
  .brand-square {
    width: 74px;
    height: 74px;
    background: var(--swoosh-grey);
    border-radius: 4px;
    flex: none;
  }
  .brand-name {
    font-family: "Lato", sans-serif;
    font-weight: 700;
    font-size: 40px;
    letter-spacing: 2px;
    color: var(--brand-green);
    line-height: 1.05;
    text-transform: uppercase;
  }
  .brand-name span { display: block; }
  .brand-rule {
    position: absolute;
    left: 166px;
    top: 338px;
    width: 260px;
    height: 2px;
    background: var(--rule-grey);
  }
  .contact-block {
    position: absolute;
    right: 70px;
    top: 150px;
    width: 420px;
    text-align: right;
    font-family: "Lato", sans-serif;
    color: var(--ink-white);
  }
  .contact-name {
    font-weight: 700;
    font-size: 34px;
    line-height: 1.1;
  }
  .contact-role {
    font-weight: 400;
    font-size: 24px;
    margin-top: 4px;
  }
  .contact-lines {
    list-style: none;
    margin-top: 56px;
  }
  .contact-line {
    display: flex;
    justify-content: flex-end;
    align-items: center;
    gap: 14px;
    font-size: 21px;
    margin-bottom: 20px;
  }
  .contact-icon {
    width: 34px;
    height: 34px;
    flex: none;
  }
</style>
</head>
<body>
<main class="canvas">
  <article class="business-card">
    <svg class="card-shapes" viewBox="0 0 1000 580" preserveAspectRatio="none" aria-hidden="true">
      <path class="grey-swoosh" d="M575,0 C515,210 450,420 345,580 L388,580 C480,420 545,210 600,0 Z" fill="#8a8b8d"/>
      <path class="green-panel" d="M612,0 C558,210 492,420 400,580 L1000,580 L1000,0 Z" fill="#22c08e"/>
    </svg>

    <div class="brand-lockup">
      <span class="brand-square"></span>
      <span class="brand-name"><span>Harwick</span><span>Partners</span></span>
    </div>
    <span class="brand-rule"></span>

    <section class="contact-block">
      <h1 class="contact-name">Danielle Frost</h1>
      <p class="contact-role">Executive Assistant</p>
      <ul class="contact-lines">
        <li class="contact-line">
          <span class="contact-text">+64 21 473 5162</span>
          <svg class="contact-icon" viewBox="0 0 34 34" aria-label="Phone">
            <circle cx="17" cy="17" r="16" fill="#ffffff"/>
            <rect x="12" y="8" width="10" height="18" rx="2" fill="none" stroke="#22c08e" stroke-width="2"/>
            <line x1="15" y1="22.5" x2="19" y2="22.5" stroke="#22c08e" stroke-width="2"/>
          </svg>
        </li>
        <li class="contact-line">
          <span class="contact-text">danielf@harwickpartners.co.nz</span>
          <svg class="contact-icon" viewBox="0 0 34 34" aria-label="Email">
            <circle cx="17" cy="17" r="16" fill="#ffffff"/>
            <rect x="9" y="11" width="16" height="12" rx="1" fill="none" stroke="#22c08e" stroke-width="2"/>
            <polyline points="9,12 17,18 25,12" fill="none" stroke="#22c08e" stroke-width="2"/>
          </svg>
        </li>
      </ul>
    </section>
  </article>
</main>
</body>
</html>
```